Web Developer Needs a Business Card Design

I need a personal business card design that represents me as a web developer for potential employers. I would like the background to be a dark color on the front for contrast with my logo and name. The back will have all my information along with a smaller version of the logo. I want something with a modern look and feel, not too conservative. This will be used for potential employers and freelance work.

Industry/Entity Type

Business

Contact Information for Business Card

Front should have my logo and name. The back should have all my personal information which would include: name: Tom Varulek, phone: 570-614-3098, email: tomvarulek@quillbox.net, website url: www.tomvarulek.net, logo, web developer.

Font styles to use
Sans Serif

Requirements
Must have
• Must include my logo. The color palette base color will be the logo color.

```html
<!DOCTYPE html>
<html lang="en">
<head>
<meta charset="utf-8">
<title>Tom Varulek — Business Card</title>
<link href="https://fonts.googleapis.com/css2?family=Arimo:wght@400;500&family=Roboto+Condensed:wght@400&display=swap" rel="stylesheet">
<style>
  :root {
    --teal: #6cc9b4;
    --ink: #07080b;
    --white: #ffffff;
    --backdrop: #e6e7e8;
  }
  * { box-sizing: border-box; margin: 0; padding: 0; }
  html, body {
    width: 1189px;
    height: 1200px;
    overflow: hidden;
    background: var(--backdrop);
  }
  .card {
    position: absolute;
    left: 140px;
    width: 918px;
    height: 523px;
    overflow: hidden;
    font-family: "Arimo", Arial, sans-serif;
  }
  .card--front { top: 46px; background: var(--ink); }
  .card--back { top: 624px; background: var(--teal); }

  .front-stripe {
    position: absolute;
    left: 0; top: 0;
    width: 119px; height: 100%;
    background: var(--teal);
  }
  .front-divider {
    position: absolute;
    left: 119px; top: 0;
    width: 10px; height: 100%;
    background: var(--white);
  }
  .front-badge {
    position: absolute;
    left: 40px; top: 30px;
    width: 240px; height: 240px;
    border-radius: 50%;
    background: var(--ink);
    display: flex;
    align-items: center;
    justify-content: center;
  }
  .front-badge__ring {
    width: 216px; height: 216px;
    border-radius: 50%;
    border: 10px solid var(--teal);
    display: flex;
    align-items: center;
    justify-content: center;
  }
  .brand-name {
    font-family: "Arimo", Arial, sans-serif;
    font-weight: 500;
    text-align: center;
    line-height: 1.1;
  }
  .front-badge .brand-name { color: var(--teal); font-size: 30px; }

  .front-identity {
    position: absolute;
    right: 44px; top: 50px;
    text-align: right;
  }
  .front-identity__name {
    color: var(--teal);
    font-size: 49px;
    font-weight: 400;
    letter-spacing: 0.5px;
    line-height: 1;
  }
  .front-identity__role {
    color: var(--white);
    font-size: 25px;
    margin-top: 10px;
    letter-spacing: 0.5px;
  }

  .contact-list {
    position: absolute;
    left: 158px; top: 339px;
    list-style: none;
  }
  .contact-list__item {
    display: flex;
    align-items: center;
    height: 52px;
    color: var(--white);
    font-size: 31px;
    letter-spacing: 0.5px;
  }
  .contact-list__icon {
    width: 18px; height: 18px;
    margin-right: 16px;
    flex: none;
  }

  .back-badge {
    position: absolute;
    left: 318px; top: 58px;
    width: 280px; height: 280px;
    border-radius: 50%;
    border: 11px solid var(--white);
    display: flex;
    align-items: center;
    justify-content: center;
  }
  .back-badge .brand-name { color: var(--white); font-size: 40px; }
  .back-name {
    position: absolute;
    left: 0; width: 100%;
    top: 390px;
    text-align: center;
    color: var(--white);
    font-family: "Roboto Condensed", "Arial Narrow", sans-serif;
    font-size: 72px;
    letter-spacing: 1px;
    line-height: 1;
  }
</style>
</head>
<body>
  <section class="card card--front">
    <div class="front-stripe"></div>
    <div class="front-divider"></div>
    <div class="front-badge">
      <div class="front-badge__ring">
        <span class="brand-name">Tom<br>Varulek</span>
      </div>
    </div>
    <header class="front-identity">
      <h1 class="front-identity__name">Tom Varulek</h1>
      <p class="front-identity__role">web developer</p>
    </header>
    <ul class="contact-list">
      <li class="contact-list__item">
        <svg class="contact-list__icon" viewBox="0 0 18 18" aria-hidden="true">
          <rect width="18" height="18" fill="#6cc9b4"/>
          <path d="M6 3.5 L8 6.5 L7 8 Q8 10.5 10 11 L11.5 10 L14.5 12 L13 14.5 Q7 14 4 6 Z" fill="#07080b"/>
        </svg>
        570-614-3098
      </li>
      <li class="contact-list__item">
        <svg class="contact-list__icon" viewBox="0 0 18 18" aria-hidden="true">
          <rect width="18" height="18" fill="#6cc9b4"/>
          <rect x="3" y="5" width="12" height="8" fill="none" stroke="#07080b" stroke-width="1.4"/>
          <path d="M3 5 L9 10 L15 5" fill="none" stroke="#07080b" stroke-width="1.4"/>
        </svg>
        tomvarulek@quillbox.net
      </li>
      <li class="contact-list__item">
        <svg class="contact-list__icon" viewBox="0 0 18 18" aria-hidden="true">
          <rect width="18" height="18" fill="#6cc9b4"/>
          <circle cx="9" cy="9" r="5.5" fill="none" stroke="#07080b" stroke-width="1.4"/>
          <ellipse cx="9" cy="9" rx="2.3" ry="5.5" fill="none" stroke="#07080b" stroke-width="1.2"/>
          <line x1="3.5" y1="9" x2="14.5" y2="9" stroke="#07080b" stroke-width="1.2"/>
        </svg>
        www.tomvarulek.net
      </li>
    </ul>
  </section>

  <section class="card card--back">
    <div class="back-badge">
      <span class="brand-name">Tom<br>Varulek</span>
    </div>
    <h2 class="back-name">TOM VARULEK</h2>
  </section>
</body>
</html>
```